Letterhead Design for Law Firm

**Edit: I have added the photo of a bottom that I like.

------
We are looking for a re-design of our new letterhead. The letterhead is for a law firm and will be used for digital and traditionally printed correspondence.

Here are some suggestions:

- Please use colours are #8ec900 and simple black.
- Please do not use any type of "waves" at the bottom of the page. This is not in style at all.
- Please stay modern yet conservative.
- Please use font Segoe UI Light or similar if you can
- Avoid clipart or illustrations.
- Utilize ample white space in the layout so the design looks clean and information is easy to read at a glance. Don't overcrowd the letterhead.
- Make sure the letterhead design is consistent with our brand identity (see corvelith.ca)
-Please, no black headers or footers.

I am attaching my current letterhead and signature for your convenience.

Remember, the letterhead is an extension of our professional identity. We are a successful firm and trial lawyers who correspond with insurers, judges, lawyers, courts, clients, etc. Make it new, modern, attractive, yet powerful and conservative.

It needs to be easily printable. I would like the bleed removed in print so the black bar the bottom crosses the page (but the text is not near the edges)
Updates

Low design quality

Target Market(s)

Clients, Government Offices, Judiciary, Lawyers, Insurance Companies, Colleagues.

Industry/Entity Type

Law

Other font styles liked:
• Segoe UI LIght, Calibri Light,

Colors
00AB8E
00BBA5
67D7C9
C6EFE9
E9F9F6

Requirements
Must have
• Everything that is on the letterhead now.
Nice to have
• Cutting Edge design, yet conservative.
Should not have
• law firm cliche design, images,

```html
<!DOCTYPE html>
<html lang="en">
<head>
<meta charset="utf-8">
<title>Verholt Personal Injury Lawyers – Letterhead</title>
<link href="https://fonts.googleapis.com/css2?family=Open+Sans:wght@300;400;600;700&display=swap" rel="stylesheet">
<style>
  :root {
    --brand-green: #8ec900;
    --band-green: #86b920;
    --ink: #111111;
    --ink-soft: #333333;
    --paper: #ffffff;
    --backdrop: #e4e5e7;
    --rule: #444444;
  }
  * { margin: 0; padding: 0; box-sizing: border-box; }
  html, body { width: 1200px; height: 874px; overflow: hidden; }
  body {
    background: var(--backdrop);
    font-family: "Open Sans", "Segoe UI", sans-serif;
    color: var(--ink);
  }
  .letterhead {
    position: absolute;
    left: 300px; top: 49px;
    width: 600px; height: 776px;
    background: var(--paper);
    box-shadow: 0 2px 10px rgba(0,0,0,.12);
    overflow: hidden;
  }
  .firm-name {
    position: absolute; left: 52px; top: 58px;
    font-weight: 400; color: var(--ink); line-height: 1.1;
  }
  .firm-name .firm-main { display: block; font-size: 38px; letter-spacing: 1px; }
  .firm-name .firm-sub { display: block; font-size: 12.5px; letter-spacing: 1.6px; }
  .contact-block {
    position: absolute; left: 408px; top: 40px;
    padding-left: 10px;
    border-left: 1.5px solid var(--brand-green);
    font-size: 8px; line-height: 1.35; color: var(--ink-soft);
    font-style: normal;
  }
  .contact-block .web-accent { color: var(--brand-green); }
  .contact-block b { font-weight: 700; color: var(--ink); }
  .contact-block .practice { margin-top: 7px; }
  .letter-body {
    position: absolute; left: 52px; top: 134px; width: 488px;
    font-size: 10.5px; line-height: 1.45; font-weight: 300;
  }
  .letter-body .strong { font-weight: 700; }
  .letter-body p { margin-bottom: 11px; }
  .re-line { display: flex; gap: 100px; margin-top: 4px; }
  .re-subject { font-weight: 700; line-height: 1.45; }
  .re-subject sup { font-size: 7px; line-height: 0; }
  .re-rule {
    margin: 8px 0 0 0;
    border: 0;
    border-top: 1px solid var(--rule);
  }
  .sign-off {
    position: absolute; left: 250px; top: 540px;
    font-size: 10.5px; line-height: 1.45; font-weight: 300;
  }
  .sign-off .firm-caps { font-weight: 400; }
  .signature-area {
    width: 120px; height: 34px; margin: 4px 0 2px;
    background: linear-gradient(90deg, #e9e9e9, #f4f4f4);
    border-radius: 3px;
  }
  .sign-off .corp { font-weight: 600; font-size: 10px; }
  .footer-band {
    position: absolute; left: 0; right: 0; bottom: 0;
    height: 34px;
    background: var(--band-green);
  }
  .footer-line {
    position: absolute; left: 0; right: 0; bottom: 40px;
    height: 2px;
    background: var(--brand-green);
  }
</style>
</head>
<body>
  <main class="letterhead">
    <div class="firm-name">
      <span class="firm-main">VERHOLT</span>
      <span class="firm-sub">PERSONAL INJURY LAWYERS</span>
    </div>

    <address class="contact-block">
      www.<span class="web-accent">CORVELITH</span>.ca<br>
      48 Harbour Street E., Suite 910<br>
      Hamilton, ON L8R 2K7<br>
      <b>T:</b> 905-555-0142<br>
      <b>F:</b> 905-555-0178<br>
      <b>File Clerk:</b> Dana Whitcombe<br>
      <b>Email:</b> dana@corvelith.ca
      <div class="practice">
        <b>Practice Restricted</b><br>
        Serious Personal Injury<br>
        Wrongful Death Litigation<br>
        Long-Term Disability Litigation<br>
        Wrongful Dismissal Litigation<br>
        Employee Terminations
      </div>
    </address>

    <section class="letter-body">
      <p class="strong">Without Prejudice</p>
      <p>March 13, 2024</p>
      <p class="strong">By Email</p>
      <p>Northvale Insurance Company<br>
        Claims Litigation Department<br>
        240 Elmridge Road South<br>
        P.O. Box 3100<br>
        Waterloo, ON&nbsp;&nbsp; N2K 1B8</p>
      <p>Attention:&nbsp; Mr. Colin Marsh</p>
      <p>Mr. Marsh:</p>
      <div class="re-line">
        <span class="strong">Re:</span>
        <span class="re-subject">Haldane v. Ferris et al.<br>
          DOL:&nbsp; September 12, 2019<br>
          Pre-Mediation Settlement Proposal – March 13<sup>th</sup>, 2024</span>
      </div>
      <hr class="re-rule">
    </section>

    <section class="sign-off">
      Yours very truly,<br>
      <span class="firm-caps">VERHOLT PERSONAL INJURY LAWYERS</span>
      <div class="signature-area" role="img" aria-label="Handwritten signature of Owen T. Verholt"></div>
      Owen T. Verholt<br>
      <span class="corp">Verholt Law Professional Corporation</span><br>
      /dw<br>
      Encl.
    </section>

    <div class="footer-line" aria-hidden="true"></div>
    <div class="footer-band" aria-hidden="true"></div>
  </main>
</body>
</html>
```